Business card design for new eCommerce site focusing on integrity and strong businsess tactics

We need a business card that will stand out and be memorable. Something with color that matches our company logo colors. Think high end version of Pactivo. There are 2 logos provided. The parent company is called Amber Ledge Partners and we are presenting a new and very exciting eCommerce site called BrightHarborTrade.example.

Target Market(s)

Our target markets are in the Activities, Food and Beverage, Health and Beauty

Industry/Entity Type

Marketing

Contact Information for Business Card

We have 4 members that need cards...I will provide all info to the winner of the design contest
Business Address is
4870 West 63rd Avenue, Suite C207
Phoenix AZ 85731

Font styles to use
Serif
Sans Serif

Colors

Designer to choose colors to be used in the design.

Requirements
Must have
• The card must be memorable...should be unique in design but must exude integrity and be playful .
• I have provided several colors or our parent company...please feel free to use which ever
Nice to have
• I will leave this up to you. Feel free to use other images of your choosing that wraps around our client.....Activities, Dining, Health, Beauty
Should not have
• just dont be boring

```html
<!DOCTYPE html>
<html lang="en">
<head>
<meta charset="utf-8">
<title>Amber Ledge Partners – Business Card</title>
<link href="https://fonts.googleapis.com/css2?family=Montserrat:wght@400;500;600;700&display=swap" rel="stylesheet">
<style>
  :root {
    --backdrop: #e4e4e4;
    --paper: #ffffff;
    --brand-blue: #2d7db3;
    --brand-green: #9bc53d;
    --ink-grey: #5f5f5f;
    --rule-grey: #bdbdbd;
    --white: #ffffff;
  }
  * { margin: 0; padding: 0; box-sizing: border-box; }
  html, body {
    width: 1200px; height: 960px; overflow: hidden;
    background: var(--backdrop);
    font-family: "Montserrat", sans-serif;
  }
  .card {
    position: absolute; top: 330px;
    width: 540px; height: 300px;
    overflow: hidden;
  }
  .card-front { left: 40px; background: var(--paper); }
  .card-back { left: 620px; background: var(--brand-blue); }

  /* front */
  .mark-circle {
    position: absolute; left: 52px; top: 32px;
    width: 82px; height: 82px; border-radius: 50%;
    background: var(--brand-green);
  }
  .company-name {
    position: absolute; left: 30px; top: 146px;
    font-size: 25px; font-weight: 700; color: var(--brand-green);
    letter-spacing: 0.2px;
  }

  .person { position: absolute; right: 30px; top: 168px; text-align: right; }
  .person-name { font-size: 18px; font-weight: 600; color: var(--brand-blue); letter-spacing: 0.3px; }
  .person-title { font-size: 13px; font-weight: 500; color: var(--ink-grey); margin-top: 2px; }

  .divider { position: absolute; left: 30px; right: 30px; top: 218px; height: 1px; background: var(--rule-grey); }

  .address { position: absolute; left: 30px; top: 232px; font-size: 11.5px; line-height: 18px; color: var(--ink-grey); letter-spacing: 0.3px; }

  .contact-list { position: absolute; right: 28px; top: 228px; list-style: none; }
  .contact-list li { display: flex; justify-content: flex-end; align-items: center; gap: 10px; font-size: 11.5px; line-height: 17px; color: var(--ink-grey); letter-spacing: 0.3px; }
  .contact-list svg { width: 10px; height: 10px; fill: none; stroke: var(--brand-blue); stroke-width: 1.6; }

  .base-band { position: absolute; left: 0; bottom: 0; width: 540px; height: 28px; }

  /* back */
  .back-brand { position: absolute; right: 28px; top: 206px; }
  .back-brand-row { display: flex; align-items: center; gap: 8px; }
  .back-dot { width: 16px; height: 16px; border-radius: 50%; background: var(--white); }
  .back-name { font-size: 19px; font-weight: 600; color: var(--white); }
  .back-tagline { margin-top: 4px; margin-left: 24px; font-size: 11px; color: var(--white); letter-spacing: 1px; }
  .back-web { margin-top: 3px; margin-left: 24px; font-size: 11px; color: var(--white); letter-spacing: 0.8px; }
</style>
</head>
<body>

<section class="card card-front" aria-label="Card front">
  <span class="mark-circle"></span>
  <span class="company-name">Amber Ledge Partners</span>

  <div class="person">
    <div class="person-name">Daniel Weaver</div>
    <div class="person-title">Founder</div>
  </div>

  <div class="divider"></div>

  <p class="address">4870 West 63rd Avenue,<br>Suite C207 Phoenix AZ 85731</p>

  <ul class="contact-list">
    <li>0413 555 019
      <svg viewBox="0 0 10 10"><rect x="2.5" y="0.8" width="5" height="8.4" rx="1"/></svg></li>
    <li>info@brightharbortrade.example
      <svg viewBox="0 0 10 10"><rect x="0.8" y="2" width="8.4" height="6"/><path d="M0.8 2 L5 5.5 L9.2 2"/></svg></li>
    <li>www.brightharbortrade.example
      <svg viewBox="0 0 10 10"><circle cx="4.2" cy="4.2" r="3"/><path d="M6.4 6.4 L9.2 9.2"/></svg></li>
  </ul>

  <svg class="base-band" viewBox="0 0 540 28" preserveAspectRatio="none">
    <path d="M0 6 L195 6 Q212 6 222 14 Q230 19 245 19 L540 19 L540 28 L0 28 Z" fill="var(--brand-blue)"/>
    <path d="M228 12 L540 8 L540 14 L240 17 Z" fill="var(--brand-green)"/>
  </svg>
</section>

<section class="card card-back" aria-label="Card back">
  <div class="back-brand">
    <div class="back-brand-row">
      <span class="back-dot"></span>
      <span class="back-name">BrightHarborTrade.example</span>
    </div>
    <div class="back-tagline">Activities-Dining-Health-Beauty</div>
    <div class="back-web">www.amberledgepartners.example</div>
  </div>
</section>

</body>
</html>
```